Valdane Companies Business Card Design

We need a new business card for our Private Equity Real Estate Development firm, “Valdane” and our EB-5 regional center “Thornmere Regional Center” on one card. We prefer a design that is simple, elegant, and represents the luxury products we design and build as well as the financial security and stability our successful history has produced. We are an industry leader in our field and 3rd generation family business that has evolved into an institutional quality investment platform. Considered design size is standard business card dimensions (3.5 x 2 inches with an additional 1/8 inch space for design elements or backgrounds that extend beyond the finished size of your piece.

Target Market(s)

• High net worth individuals
• Highly skilled technical workers and physicians in the US seeking investment-based immigration opportunities
• Sophisticated private equity investors
• Intermediary partners include domestic attorneys and investment brokers, as well as international agent networks
• US real estate developers

Industry/Entity Type

Finance

Contact Information for Business Card

(Providing placeholder info for personal information, please design for longer character spaces, longer names and addresses etc..)
• Logo for Valdane
• Logo for Thornmere Regional Center
• Full name: Marcus Valdane
• Job title: CEO
• Email address: mvaldane@valdanecompanies.com
• Cell phone number: +1.555.314.2287
• Office number +1.555.628.4410
• Office address: Larkfield Court 5, 4817 Vista Orilla, Ashcombe, NV.
• Website: www.valdanecompanies.com

Font styles to use
Serif
Sans Serif

Colors
ec1f27
ffffff
000000

Requirements
Must have
• • Logo for Valdane
• • Logo for Thornmere Regional Center
• - Use rounded corners
• (See .ai file included for logos)
Nice to have
• • Simple, elegant design
• • Aesthetically compatible with our website design (www.valdanecompanies.com)
• • Color palette including but not limited to white, black, and red (as per logos)
Should not have
• - Not too much red color
• - Do not stack both logos on top of each other

```html
<!DOCTYPE html>
<html lang="en">
<head>
<meta charset="utf-8">
<title>Valdane Companies Business Card</title>
<link rel="stylesheet" href="https://fonts.googleapis.com/css2?family=Cinzel:wght@700&family=Roboto:wght@400;700&display=swap">
<style>
  :root {
    --stage: #262626;
    --card-dark: #1f1f1f;
    --card-light: #ffffff;
    --ink: #000000;
    --ink-soft: #1a1a1a;
    --silver: #d9d9d9;
    --accent: #ec1f27;
    --rule: #2b2b2b;
  }
  * { margin: 0; padding: 0; box-sizing: border-box; }
  html, body {
    width: 1200px;
    height: 1200px;
    overflow: hidden;
    background: var(--stage);
  }
  .canvas {
    position: relative;
    width: 1200px;
    height: 1200px;
  }
  .card {
    position: absolute;
    left: 250px;
    width: 700px;
    height: 400px;
    border-radius: 14px;
  }
  .card--front {
    top: 160px;
    background: var(--card-dark);
    display: flex;
    align-items: center;
    justify-content: center;
  }
  .card--back {
    top: 640px;
    background: var(--card-light);
  }
  .brand {
    display: flex;
    align-items: center;
    gap: 18px;
    font-family: "Cinzel", Georgia, serif;
    font-weight: 700;
    letter-spacing: 0.04em;
  }
  .brand__mark {
    width: 22px;
    height: 22px;
    flex: none;
  }
  .brand--regional {
    color: var(--silver);
    font-size: 34px;
  }
  .brand--regional .brand__mark { background: var(--silver); }
  .brand--capital {
    position: absolute;
    left: 50px;
    top: 178px;
    color: var(--ink-soft);
    font-size: 30px;
  }
  .brand--capital .brand__mark { background: var(--ink-soft); }
  .divider {
    position: absolute;
    left: 400px;
    top: 110px;
    width: 1px;
    height: 180px;
    background: var(--rule);
  }
  .contact {
    position: absolute;
    left: 425px;
    top: 104px;
    font-family: "Roboto", Arial, sans-serif;
    color: var(--ink);
  }
  .contact__name {
    font-size: 22px;
    font-weight: 700;
    line-height: 1.2;
  }
  .contact__title {
    font-size: 15px;
    color: var(--accent);
    line-height: 1.4;
  }
  .contact__address {
    font-size: 14px;
    line-height: 1.3;
    margin-bottom: 12px;
  }
  .contact__list { list-style: none; }
  .contact__item {
    display: flex;
    align-items: center;
    gap: 10px;
    font-size: 13px;
    line-height: 1.65;
  }
  .contact__icon {
    width: 13px;
    height: 13px;
    flex: none;
    fill: none;
    stroke: var(--accent);
    stroke-width: 1.6;
  }
</style>
</head>
<body>
<main class="canvas">

  <section class="card card--front" aria-label="Card front">
    <div class="brand brand--regional">
      <span class="brand__mark"></span>
      <span class="brand__name">Thornmere Regional Center</span>
    </div>
  </section>

  <section class="card card--back" aria-label="Card back">
    <div class="brand brand--capital">
      <span class="brand__mark"></span>
      <span class="brand__name">Valdane Capital</span>
    </div>

    <div class="divider"></div>

    <div class="contact">
      <p class="contact__name">Marcus Valdane</p>
      <p class="contact__title">CEO</p>
      <p class="contact__address">Larkfield Court 5, 4817<br>Vista Orilla Ashcombe, NV</p>
      <ul class="contact__list">
        <li class="contact__item">
          <svg class="contact__icon" viewBox="0 0 14 14" aria-hidden="true"><rect x="3.5" y="1" width="7" height="12" rx="1.2"/><line x1="6" y1="11" x2="8" y2="11"/></svg>
          <span>+1.555.314.2287</span>
        </li>
        <li class="contact__item">
          <svg class="contact__icon" viewBox="0 0 14 14" aria-hidden="true"><path d="M1.5 5.5 C4 2.5 10 2.5 12.5 5.5 L11 7 L9.5 5.8 L9.5 4.8 C8 4.2 6 4.2 4.5 4.8 L4.5 5.8 L3 7 Z"/><rect x="3" y="8" width="8" height="4.5" rx="0.8"/></svg>
          <span>+1.555.628.4410</span>
        </li>
        <li class="contact__item">
          <svg class="contact__icon" viewBox="0 0 14 14" aria-hidden="true"><rect x="1" y="3" width="12" height="8.5" rx="0.8"/><polyline points="1,3.5 7,8 13,3.5"/></svg>
          <span>mvaldane@valdanecompanies.com</span>
        </li>
        <li class="contact__item">
          <svg class="contact__icon" viewBox="0 0 14 14" aria-hidden="true"><circle cx="7" cy="7" r="5.8"/><ellipse cx="7" cy="7" rx="2.5" ry="5.8"/><line x1="1.2" y1="7" x2="12.8" y2="7"/></svg>
          <span>www.valdanecompanies.com</span>
        </li>
      </ul>
    </div>
  </section>

</main>
</body>
</html>
```